Sleek wordpress site for Bramblecrest finishing works

We are a commercial job shop that serves B2B, govt & LEO and retail clients.We need a wordpress site with 6 individual pages: homepage, coating, laser engraving, laser cutting, part marking, and contact us. I have attached an outline of the desired flow and sub headings for each page. I would like to incorporate the colors of the logo through out the site to be clean and sleek enough to appeal to B2B commercial clients yet be inviting enough for retail clients.

I would like to have easy picture functionality so photographs on each page can be updated easily.

Target Market(s)

B2B industrial & Govt and Military part marking, laser engraving and coating: machine shops, aerospace companies, tool manufactures. Retail: personalized gifts, Job Shop

Coding

Coded - Design and coding required

Font styles to use
Sans Serif
Other font styles liked:
• Open to suggestion

Colors
0255a3
3176b5
eaf1f7
cfdeed
ffffff

Requirements
Must have
• Clean easy to navigate flow, separate pages as indicated on attached outline, high class feel. Great picture functionality, professional and inviting feel,
• **update: needs to be optimized for mobile, should have a gallery function. Gallery can be an additional page or embedded
Nice to have
• Social media connectivity links,
Should not have
• crappy plugins that make back-end management difficult, no blog

```html
<!DOCTYPE html>
<html lang="en">
<head>
<meta charset="utf-8">
<title>Bramblecrest Finishing Works</title>
<link rel="stylesheet" href="https://fonts.googleapis.com/css2?family=Lato:ital,wght@0,400;0,700;0,900;1,400&family=Roboto:wght@400;500;700&display=swap">
<style>
:root{
  --blue:#0a3f96;
  --blue-bright:#0255a3;
  --blue-mid:#3176b5;
  --blue-pale:#eaf1f7;
  --blue-soft:#cfdeed;
  --ink:#1b1b1b;
  --text:#555a60;
  --ghost:#e9ecef;
  --footer:#141414;
  --footer-text:#d8d8d8;
  --white:#ffffff;
}
*{margin:0;padding:0;box-sizing:border-box}
html,body{width:1200px;height:3000px;overflow:hidden;background:var(--white)}
body{position:relative;font-family:'Roboto',sans-serif;color:var(--text)}
.abs{position:absolute}

/* header */
.topline{left:0;top:0;width:1200px;height:4px;background:var(--blue)}
.brand{left:96px;top:28px;display:flex;align-items:center;gap:12px}
.brand-dot{width:34px;height:34px;border-radius:50%;background:var(--blue)}
.brand-name{font-family:'Lato',sans-serif;font-weight:900;font-size:17px;line-height:1.15;color:var(--blue);width:140px;text-transform:uppercase}
.contact-bar{right:98px;top:30px;font-size:14px;color:#555;display:flex;align-items:center;gap:10px}
.contact-bar svg{width:13px;height:13px;fill:var(--blue)}
.contact-bar .sep{color:#999;margin:0 6px}
.nav{right:98px;top:76px;display:flex;gap:26px;font-family:'Roboto',sans-serif;font-weight:500;font-size:14px;color:#111;text-transform:uppercase}
.nav .active{color:var(--blue)}

/* hero */
.hero{left:0;top:116px;width:1200px;height:640px;background:radial-gradient(ellipse at 78% 42%,#e9a94b 0%,#a9662a 14%,#4f3a2e 38%,#2a2c33 70%,#1d2026 100%)}
.hero-curve{left:0;top:560px;width:1200px;height:200px}
.hero-title{left:100px;top:282px;font-family:'Lato',sans-serif;font-weight:700;font-size:42px;color:var(--white)}
.hero-text{left:100px;top:354px;width:560px;font-family:'Lato',sans-serif;font-weight:700;font-size:21px;line-height:32px;color:var(--white)}
.btn{display:inline-flex;align-items:center;justify-content:center;gap:8px;background:var(--blue);color:var(--white);font-family:'Roboto',sans-serif;font-weight:700;font-size:16px;border-radius:24px;text-transform:uppercase}
.hero-btn{left:100px;top:448px;width:198px;height:48px}
.arrow-dot{width:36px;height:36px;border-radius:50%;background:rgba(0,0,0,.75);display:flex;align-items:center;justify-content:center}
.arrow-dot svg{width:12px;height:12px;stroke:#fff;stroke-width:2.6;fill:none}

/* section titles */
.ghost{font-family:'Lato',sans-serif;font-weight:900;color:var(--ghost);text-transform:uppercase;white-space:nowrap}
.title{font-family:'Lato',sans-serif;font-weight:900;color:var(--ink);text-transform:uppercase;white-space:nowrap}

/* services */
.services-ghost{left:0;width:1200px;top:806px;text-align:center;font-size:72px}
.services-title{left:0;width:1200px;top:832px;text-align:center;font-size:36px}
.services-sub{left:0;width:1200px;top:896px;text-align:center;font-size:13px;color:#666}
.service{width:340px;text-align:center}
.service-icon{width:120px;height:140px;margin:0 auto}
.service h3{margin-top:18px;font-family:'Roboto',sans-serif;font-weight:500;font-size:19px;color:#111;text-transform:uppercase}
.service p{margin-top:16px;font-size:13px;line-height:24px;color:#666}
.slide-arrow svg{width:18px;height:18px;stroke:#555;stroke-width:2.2;fill:none}

/* tiles */
.tiles{left:0;top:1306px;width:1200px;height:276px;display:flex}
.tile{width:300px;height:276px;position:relative}
.tile span{position:absolute;left:0;width:300px;text-align:center;font-family:'Lato',sans-serif;font-weight:700;font-size:24px;text-transform:uppercase}
.t1{background:linear-gradient(160deg,#8c96a6 0%,#4a5a74 45%,#1e2f58 100%)}
.t2{background:linear-gradient(180deg,#3b3e44 0%,#6d7076 50%,#2a2c30 100%)}
.t3{background:radial-gradient(ellipse at 50% 60%,#d28a5a 0%,#6a3f45 35%,#24242c 80%)}
.t4{background:radial-gradient(ellipse at 60% 50%,#b07a5a 0%,#46372f 45%,#1f1c1c 90%)}
.faded{color:rgba(255,255,255,.28);bottom:16px}
.bright{color:#fff;top:120px}

/* about */
.about-ghost{left:752px;top:1600px;font-size:70px}
.about-title{left:98px;top:1668px;font-size:35px}
.about-text{left:98px;width:544px;font-size:12.5px;line-height:24px;color:#666}
.about-btn{left:98px;top:1938px;width:160px;height:46px}
.video-frame{left:732px;top:1682px;width:402px;height:268px;border:3px solid var(--blue)}
.video{left:698px;top:1716px;width:402px;height:268px;background:radial-gradient(ellipse at 42% 55%,#f7c8b0 0%,#d64a3a 22%,#8d2a30 50%,#3a2a30 80%),#3a2a30;border:4px solid #fff;box-shadow:0 0 0 1px #ddd}
.video-teal{left:1010px;top:1900px;width:90px;height:84px;background:linear-gradient(135deg,transparent 40%,#38a9c8 40%)}
.play{left:876px;top:1828px;width:44px;height:44px;border-radius:50%;background:#fff;display:flex;align-items:center;justify-content:center}
.divider{left:98px;top:2084px;width:1004px;height:1px;background:#ddd}

/* clients + testimonials */
.clients-ghost{left:0;top:2144px;font-size:46px}
.clients-title{left:98px;top:2158px;font-size:23px}
.testi-ghost{left:828px;top:2144px;font-size:46px}
.testi-title{left:628px;top:2158px;font-size:23px}
.small-arrows{display:flex;gap:14px}
.small-arrows svg{width:10px;height:12px;stroke:#555;stroke-width:2;fill:none}
.client{width:146px;height:76px;border:1px solid #e3e3e3;background:#fff;display:flex;align-items:center;justify-content:center;font-family:'Lato',sans-serif;font-weight:700;font-size:15px;color:#333;text-align:center;line-height:1.2;box-shadow:0 1px 3px rgba(0,0,0,.06)}
.testimonial{left:628px;top:2220px;width:472px;height:130px;background:#dedede;border:3px solid #cfcfcf;padding:20px 24px 0 30px;font-family:'Lato',sans-serif;font-style:italic;font-size:12px;line-height:24px;color:#5a6f9a}
.testimonial b{font-style:normal;font-size:26px;color:#888;position:absolute;left:14px;top:10px}
.testi-tail{left:660px;top:2348px;width:0;height:0;border-left:14px solid transparent;border-right:14px solid transparent;border-top:14px solid #cfcfcf}
.testi-name{left:708px;top:2376px;font-family:'Lato',sans-serif;font-weight:700;font-size:19px;color:#333}
.testi-name i{font-weight:400;font-size:13px;color:#666}

/* footer */
.footer-curve{left:0;top:2470px;width:1200px;height:140px}
.footer{left:0;top:2600px;width:1200px;height:400px;background:var(--footer)}
.f-head{font-family:'Lato',sans-serif;font-weight:700;font-size:19px;color:var(--white);text-transform:uppercase}
.f-head em{font-style:normal;color:var(--blue-mid)}
.links{list-style:none;font-size:13px;line-height:26px;color:var(--footer-text)}
.links li::before{content:"»";color:#fff;margin-right:12px}
.f-row{display:flex;gap:18px;font-size:13px;line-height:26px;color:var(--footer-text)}
.f-row svg{width:14px;height:14px;fill:#fff;margin-top:6px;flex:none}
.hours{display:grid;grid-template-columns:96px auto;font-size:13px;line-height:20px}
.quote-text{font-size:13px;line-height:26px;color:var(--footer-text);width:460px}
.field{width:228px;height:44px;border:1px solid #ccc;font-size:11px;color:#ddd;padding:14px 10px}
.submit{width:228px;height:42px;background:var(--blue);color:#fff;font-family:'Roboto',sans-serif;font-weight:700;font-size:16px;display:flex;align-items:center;justify-content:center;text-transform:uppercase}
.f-line{left:98px;top:2894px;width:1004px;height:1px;background:#555}
.copyright{left:98px;top:2938px;font-size:14px;color:var(--footer-text)}
.follow{left:830px;top:2934px;font-family:'Lato',sans-serif;font-weight:700;font-size:21px;color:#fff;display:flex;align-items:center;gap:8px;text-transform:uppercase}
.follow em{font-style:normal;color:var(--blue-mid);margin-right:10px}
.social{width:28px;height:28px;border:2px solid #fff;border-radius:50%}
</style>
</head>
<body>

<!-- header -->
<div class="abs topline"></div>
<div class="abs brand">
  <div class="brand-dot"></div>
  <div class="brand-name">Bramblecrest Finishing Works</div>
</div>
<div class="abs contact-bar">
  <svg viewBox="0 0 24 24"><path d="M6.6 10.8c1.4 2.8 3.8 5.1 6.6 6.6l2.2-2.2c.3-.3.7-.4 1-.2 1.1.4 2.3.6 3.6.6.6 0 1 .4 1 1V20c0 .6-.4 1-1 1C10.6 21 3 13.4 3 4c0-.6.4-1 1-1h3.5c.6 0 1 .4 1 1 0 1.3.2 2.5.6 3.6.1.3 0 .7-.2 1z"/></svg>
  <span>480.555.0174</span><span class="sep">|</span>
  <svg viewBox="0 0 24 24"><path d="M2 5h20v14H2z M2 5l10 8 10-8" fill="none" stroke="#0a3f96" stroke-width="2.4"/></svg>
  <span>hello@bramblecrestworks.com</span>
</div>
<nav class="abs nav">
  <span class="active">Home</span><span>Coating</span><span>Laser Engraving</span><span>Laser Cutting</span><span>Part Marking</span><span>Contact</span>
</nav>

<!-- hero -->
<div class="abs hero" role="img" aria-label="Laser cutting head throwing a shower of orange sparks over a metal part"></div>
<svg class="abs hero-curve" viewBox="0 0 1200 200" preserveAspectRatio="none">
  <path d="M0 60 Q600 240 1200 40 L1200 200 L0 200 Z" fill="#ffffff"/>
  <path d="M0 78 Q600 244 1200 56 L1200 72 Q600 196 0 96 Z" fill="#0a3f96"/>
</svg>
<div class="abs arrow-dot" style="left:40px;top:366px"><svg viewBox="0 0 12 12"><path d="M8 1 L3 6 L8 11"/></svg></div>
<div class="abs arrow-dot" style="left:1124px;top:366px"><svg viewBox="0 0 12 12"><path d="M4 1 L9 6 L4 11"/></svg></div>
<h1 class="abs hero-title">BRAMBLECREST FINISHING</h1>
<p class="abs hero-text">Duraglaze is a spray on ceramic based finish that can be applied to metals, plastics, polymers and wood.</p>
<div class="abs btn hero-btn">Read More
  <svg width="16" height="16" viewBox="0 0 16 16"><circle cx="8" cy="8" r="7.5" fill="#fff"/><path d="M6 4.5 L9.5 8 L6 11.5" stroke="#0a3f96" stroke-width="2" fill="none"/></svg>
</div>

<!-- services -->
<div class="abs ghost services-ghost">Our Services</div>
<h2 class="abs title services-title">Our Services</h2>
<p class="abs services-sub">We offer the wide range of services to help our customer's create whatever they needs</p>
<div class="abs slide-arrow" style="left:38px;top:1080px"><svg viewBox="0 0 18 18"><path d="M12 2 L5 9 L12 16"/></svg></div>
<div class="abs slide-arrow" style="left:1144px;top:1080px"><svg viewBox="0 0 18 18"><path d="M6 2 L13 9 L6 16"/></svg></div>

<div class="abs service" style="left:76px;top:952px">
  <svg class="service-icon" viewBox="0 0 120 140">
    <path d="M60 4 A56 56 0 0 1 90 108 L60 136 L30 108 A56 56 0 0 1 60 4 Z" fill="#0a3f96"/>
    <circle cx="60" cy="60" r="46" fill="#ffffff"/><circle cx="60" cy="60" r="41" fill="#0a3f96"/>
    <rect x="42" y="44" width="30" height="34" rx="2" fill="none" stroke="#fff" stroke-width="3"/>
    <path d="M52 64 L78 38 M68 72 L82 58" stroke="#fff" stroke-width="3" fill="none"/>
  </svg>
  <h3>Laser Engraving</h3>
  <p>Capabilities Statement: With our selection<br>of CO2 and fiber lasers there are very few materials<br>and substrates that we cannot mark</p>
</div>
<div class="abs service" style="left:430px;top:952px">
  <svg class="service-icon" viewBox="0 0 120 140">
    <path d="M60 4 A56 56 0 0 1 90 108 L60 136 L30 108 A56 56 0 0 1 60 4 Z" fill="#0a3f96"/>
    <circle cx="60" cy="60" r="46" fill="#ffffff"/><circle cx="60" cy="60" r="41" fill="#0a3f96"/>
    <circle cx="44" cy="72" r="7" fill="none" stroke="#fff" stroke-width="3"/>
    <circle cx="76" cy="72" r="7" fill="none" stroke="#fff" stroke-width="3"/>
    <path d="M49 67 L74 40 M71 67 L46 40" stroke="#fff" stroke-width="3"/>
  </svg>
  <h3>Laser Cutting</h3>
  <p>BFW can custom cut virtually any shape or design in<br>a variety of substrates or materials. Custom cut items<br>can be fabricated from wood, foam</p>
</div>
<div class="abs service" style="left:784px;top:952px">
  <svg class="service-icon" viewBox="0 0 120 140">
    <path d="M60 4 A56 56 0 0 1 90 108 L60 136 L30 108 A56 56 0 0 1 60 4 Z" fill="#0a3f96"/>
    <circle cx="60" cy="60" r="46" fill="#ffffff"/><circle cx="60" cy="60" r="41" fill="#0a3f96"/>
    <path d="M60 36 L72 60 L66 78 L54 78 L48 60 Z" fill="none" stroke="#fff" stroke-width="3"/>
    <path d="M60 36 L60 62" stroke="#fff" stroke-width="2.5"/>
    <path d="M34 44 L48 44 M72 44 L86 44" stroke="#fff" stroke-width="2.5"/>
    <rect x="56" y="32" width="8" height="8" fill="#fff"/>
  </svg>
  <h3>Part Marking</h3>
  <p>Nemo enim ipsam voluptatem quia voluptas<br>sit aspernatur aut odit aut fugit, sed quia consequ<br>tur magni dolores eos qui ratione volupta</p>
</div>

<!-- service tiles -->
<div class="abs tiles">
  <div class="tile t1" role="img" aria-label="Laser engraving machine marking a metal plate"><span class="faded">Laser Engraving</span></div>
  <div class="tile t2" role="img" aria-label="Laser cutting nozzle over a sheet of steel"><span class="bright">Laser Cutting</span></div>
  <div class="tile t3" role="img" aria-label="Part marking head with a bright spark burst"><span class="faded">Part Marking</span></div>
  <div class="tile t4" role="img" aria-label="Technician spraying coating onto a part"><span class="faded">Coatings</span></div>
</div>

<!-- about -->
<div class="abs ghost about-ghost">About Us</div>
<h2 class="abs title about-title">About Bramblecrest Finishing</h2>
<p class="abs about-text" style="top:1742px">Nemo enim ipsam voluptatem quia voluptas sit aspernatur aut odit aut fugit, sed quia conse-<br>quuntur magni dolores eos qui ratione voluptatem sequi nesciunt.</p>
<p class="abs about-text" style="top:1810px">Neque porro quisquam est, qui dolorem ipsum quia dolor sit amet, consectetur, adipisci velit, sed quia non numquam eius modi tempora incidunt ut labore et dolore magnam aliquam quaerat voluptatem. Ut enim ad minima veniam, quis nostrum exercitationem ullam corporis suscipit laboriosam, nisi ut aliquid commodi consequatu...</p>
<div class="abs btn about-btn">Read More
  <svg width="16" height="16" viewBox="0 0 16 16"><circle cx="8" cy="8" r="7.5" fill="#fff"/><path d="M6 4.5 L9.5 8 L6 11.5" stroke="#0a3f96" stroke-width="2" fill="none"/></svg>
</div>
<div class="abs video-frame"></div>
<div class="abs video" role="img" aria-label="Video still of a laser cutting head glowing red over a sheet"></div>
<div class="abs video-teal"></div>
<div class="abs play"><svg width="18" height="18" viewBox="0 0 18 18"><path d="M5 2 L16 9 L5 16 Z" fill="#0a3f96"/></svg></div>
<div class="abs divider"></div>

<!-- clients -->
<div class="abs ghost clients-ghost">Our Clients</div>
<h2 class="abs title clients-title">Our Clients</h2>
<div class="abs small-arrows" style="left:548px;top:2166px">
  <svg viewBox="0 0 10 12"><path d="M8 1 L2 6 L8 11"/></svg><svg viewBox="0 0 10 12"><path d="M2 1 L8 6 L2 11"/></svg>
</div>
<div class="abs client" style="left:98px;top:2218px">Larkfield Drinks</div>
<div class="abs client" style="left:266px;top:2218px">Corvane</div>
<div class="abs client" style="left:434px;top:2218px">Halden Cola</div>
<div class="abs client" style="left:98px;top:2316px">Ostrander Labs</div>
<div class="abs client" style="left:266px;top:2316px">Pellmont</div>
<div class="abs client" style="left:434px;top:2316px">Teagan &amp; Co</div>

<!-- testimonials -->
<div class="abs ghost testi-ghost">Testimonials</div>
<h2 class="abs title testi-title">Testimonials</h2>
<div class="abs small-arrows" style="left:1070px;top:2166px">
  <svg viewBox="0 0 10 12"><path d="M8 1 L2 6 L8 11"/></svg><svg viewBox="0 0 10 12"><path d="M2 1 L8 6 L2 11"/></svg>
</div>
<div class="abs testimonial"><b>“</b>At vero eos et accusamus et iusto odio dignissimos ducimus qui blanditiis pre sentium voluptatum deleniti atque corrupti quos dolores et quas molestias excepturi sint occaecati cupiditate non provident,</div>
<div class="abs testi-tail"></div>
<div class="abs testi-name">Marta Quill, <i>Creative Manager, USA</i></div>

<!-- footer -->
<svg class="abs footer-curve" viewBox="0 0 1200 140" preserveAspectRatio="none">
  <path d="M0 120 Q560 -20 1200 80 L1200 140 L0 140 Z" fill="#141414"/>
  <path d="M0 98 Q560 -40 1200 56 L1200 76 Q560 -14 0 116 Z" fill="#0a3f96"/>
</svg>
<div class="abs footer"></div>

<h3 class="abs f-head" style="left:98px;top:2606px">Quick <em>Links</em></h3>
<ul class="abs links" style="left:98px;top:2658px">
  <li>Home</li><li>Coating</li><li>Laser Engraving</li><li>Laser Cutting</li><li>Part Marking</li><li>Gallery</li><li>Contact Us</li>
</ul>

<h3 class="abs f-head" style="left:324px;top:2606px">Contact <em>Us</em></h3>
<div class="abs f-row" style="left:324px;top:2660px">
  <svg viewBox="0 0 24 24"><path d="M12 2a7 7 0 0 0-7 7c0 5 7 13 7 13s7-8 7-13a7 7 0 0 0-7-7zm0 9.5A2.5 2.5 0 1 1 12 6.5a2.5 2.5 0 0 1 0 5z"/></svg>
  <span>418 W Cinder Ave #12, Tempe,<br>AZ 85281</span>
</div>
<div class="abs f-row" style="left:324px;top:2726px">
  <svg viewBox="0 0 24 24"><path d="M6.6 10.8c1.4 2.8 3.8 5.1 6.6 6.6l2.2-2.2c.3-.3.7-.4 1-.2 1.1.4 2.3.6 3.6.6.6 0 1 .4 1 1V20c0 .6-.4 1-1 1C10.6 21 3 13.4 3 4c0-.6.4-1 1-1h3.5c.6 0 1 .4 1 1 0 1.3.2 2.5.6 3.6.1.3 0 .7-.2 1z"/></svg>
  <span>(+1) 480 555 0199</span>
</div>
<div class="abs f-row" style="left:324px;top:2768px">
  <svg viewBox="0 0 24 24"><circle cx="12" cy="12" r="9" fill="none" stroke="#fff" stroke-width="3"/><path d="M12 7v5l3 2" stroke="#fff" stroke-width="2.4" fill="none"/></svg>
  <div class="hours"><span>Mon - Weds:</span><span>9am-5:30pm</span><span>Thu - Fri:</span><span>9am-7pm</span><span>Sat - Sun:</span><span>11am-3pm</span></div>
</div>

<h3 class="abs f-head" style="left:632px;top:2606px">Get a <em>Quote</em></h3>
<p class="abs quote-text" style="left:632px;top:2654px">Bramblecrest Finishing offer the wide range of services to help our customer's create whatever they needs.</p>
<div class="abs field" style="left:632px;top:2724px">Name</div>
<div class="abs field" style="left:872px;top:2724px">Email</div>
<div class="abs field" style="left:632px;top:2780px">Phone No</div>
<div class="abs submit" style="left:872px;top:2782px">Submit</div>

<div class="abs f-line"></div>
<div class="abs copyright">Copyrights © 2018 Bramblecrest Finishing.&nbsp; All Rights Reserved &nbsp;&nbsp;|&nbsp;&nbsp; Privacy Policy.</div>
<div class="abs follow">Follow <em>Us</em>
  <span class="social" aria-label="Social link"></span>
  <span class="social" aria-label="Social link"></span>
  <span class="social" aria-label="Social link"></span>
  <span class="social" aria-label="Social link"></span>
</div>

</body>
</html>
```